Meal Plan Website Needs New Pages Designed

Brightwick Supper Kits is an online, membership based program that delivers weekly meal programs (7 days worth of recipes plus shopping lists) carefully crafted by an expert team of meal planners. All recipes are created to comply with the following macronutrient ratio: 65% healthy fats, 25% lean protein, 10% good carbs.
All recipes are Paleo friendly and a great resource for those individuals who want to correctly implement this type of diet.

We are re-designing our website and need the following pages designed:

· Home page w/ logo
· How it works page
· Get Started! page
· Recipes Page template (these will be the pages on our site that will have recipes)
· Kitchen Essentials Training page (this will be a page with videos and tips + tricks, PDFs, etc)

So 5 total PSDs, 1 for each page.

Target audience: Men and women between the ages of 30 and 60 who want to:
· Eat healthy
· Lose weight
· Follow/Implement the Paleo diet
· Take the guesswork out of preparing delicious AND healthy meals for them and their families
· Know exactly what to eat, what to buy, how to make it

Feelings/Messages we want to communicate through the design:
· “Organic” but elegant look
· Fresh/light/Airy
· Simple but NOT GENERIC
· “I want to get cooking” feeling

Our Stylistic preferences:
· Minimalist with a few bold elements (something in between)
· Easy to visually navigate (enough white space, but not too much)
· There is more to “see” than to “read”

Our Color Preferences:
· Lighter pallet
· Colors that evoke natural woods, granite countertops…
· Stay away from using all dark colors

Our Font Type Preferences:
· Easy to read
· Not more than 3 font types
· Not too rigid
· Not too sophisticated
· Simple with a touch

Examples of Website Designs that we like:
· http://www.dorvanta.com/meal-plans/
· http://grulvix.com/
· https://www.mistobarn.com/

```html
<!DOCTYPE html>
<html lang="en">
<head>
<meta charset="utf-8">
<title>Brightwick Supper Kits</title>
<link rel="stylesheet" href="https://fonts.googleapis.com/css2?family=Open+Sans:wght@300;400;600;700&display=swap">
<style>
:root{
  --teal:#7fc0cc;
  --teal-dark:#6fb3c0;
  --ink:#222;
  --text:#444;
  --muted:#666;
  --paper:#f7f7f7;
  --paper-2:#ececec;
  --white:#fff;
  --charcoal:#3e3e3e;
}
*{box-sizing:border-box;margin:0;padding:0}
html,body{width:1200px;height:2699px;overflow:hidden}
body{position:relative;font-family:"Open Sans",Arial,sans-serif;color:var(--text);background:var(--paper)}
.abs{position:absolute}

.hero{left:0;top:0;width:1200px;height:637px;
  background:radial-gradient(ellipse at 25% 70%,#d9623f 0,#c65a36 10%,transparent 28%),
  radial-gradient(ellipse at 75% 55%,#b56a2c 0,#a05a25 25%,transparent 55%),
  linear-gradient(120deg,#e8efe0 0%,#a9c96a 30%,#e6c55a 55%,#b87534 80%,#d9433a 100%)}
.nav{left:157px;top:86px;width:885px;height:65px;background:var(--teal);display:flex;align-items:center}
.nav a{color:var(--white);font-weight:600;font-size:17px;text-decoration:none;position:absolute;top:21px}
.logo{left:527px;top:41px;width:144px;height:144px;border-radius:50%;background:var(--charcoal);
  display:flex;flex-direction:column;align-items:center;justify-content:center;color:var(--white);
  font-weight:600;font-size:15px;line-height:1.3;text-align:center}
.arrow{width:64px;height:64px}
.caption{left:0;top:522px;width:1200px;height:115px;background:rgba(50,50,50,.72);color:var(--white);text-align:center}
.caption .lead{position:absolute;top:26px;width:100%;font-weight:700;font-size:23px}
.caption .ratio{position:absolute;top:60px;width:100%;font-weight:300;font-size:35px}

.section-title{width:1200px;text-align:center;color:var(--teal);font-weight:300;font-size:36px}

.card{width:285px}
.card .photo{width:279px;height:191px}
.card h3{margin-top:19px;font-size:13.5px;font-weight:700;color:var(--ink)}
.card p{margin-top:11px;font-size:13px;line-height:22.5px;color:var(--text);width:285px}
.card .actions{margin-top:16px;margin-left:-3px;display:flex;gap:9px}
.btn{display:inline-block;height:36px;line-height:36px;background:var(--teal);color:var(--white);
  font-size:12.5px;font-weight:700;text-align:center;text-transform:uppercase}
.btn-details{width:104px}
.btn-buy{width:105px}

.testimonials{left:0;top:1569px;width:1200px;height:653px;background:var(--paper-2)}
.avatar{left:466px;top:1697px;width:266px;height:266px;border-radius:50%;border:10px solid var(--teal);
  background:linear-gradient(135deg,#f1eee9,#d9c9bd 55%,#5a4237)}
.quote-name{top:1989px;width:1200px;text-align:center;font-size:24px;color:var(--charcoal)}
.quote-company{top:2033px;width:1200px;text-align:center;font-size:17px;color:var(--text)}
.quote-text{left:165px;top:2068px;width:870px;text-align:center;font-size:17px;line-height:29px;color:var(--text)}

.newsletter{left:0;top:2222px;width:1200px;height:113px;background:var(--teal)}
.newsletter label{position:absolute;left:147px;top:40px;font-size:20px;color:var(--ink)}
.newsletter .field{position:absolute;left:369px;top:34px;width:502px;height:45px;background:var(--white);
  font-size:15px;color:#999;padding:13px 12px}
.newsletter .submit{position:absolute;left:883px;top:34px;width:124px;height:45px;background:#2b2b2b;
  color:var(--white);font-weight:700;font-size:20px;text-align:center;line-height:45px}

.footer-col{font-size:13px;color:var(--text)}
.footer-col li{list-style:none;height:33px}
.social li{display:flex;align-items:center;height:45.5px}
.social .dot{position:absolute;left:122px;width:37px;height:37px;border-radius:50%;background:#111}
.copyright{top:2641px;width:1200px;text-align:center;font-size:13px;color:var(--ink)}
</style>
</head>
<body>

<header class="abs hero" role="img" aria-label="Photo of a plated breaded cutlet with tomato, herbs and fresh salad"></header>

<nav class="abs nav">
  <a style="left:33px">Home</a>
  <a style="left:127px">About Us</a>
  <a style="left:252px">Meal Plans</a>
  <a style="left:544px">Recipes</a>
  <a style="left:667px">FAQ's</a>
  <a style="left:773px">Contact Us</a>
</nav>
<div class="abs logo"><span>Brightwick</span><span>Supper Kits</span></div>

<svg class="abs arrow" style="left:92px;top:297px" viewBox="0 0 64 64"><circle cx="32" cy="32" r="32" fill="#444" fill-opacity=".75"/><path d="M37 18 23 32l14 14" stroke="#fff" stroke-width="6" fill="none" stroke-linecap="round"/></svg>
<svg class="abs arrow" style="left:1040px;top:297px" viewBox="0 0 64 64"><circle cx="32" cy="32" r="32" fill="#444" fill-opacity=".75"/><path d="M27 18l14 14-14 14" stroke="#fff" stroke-width="6" fill="none" stroke-linecap="round"/></svg>

<div class="abs caption">
  <p class="lead">All recipes are created to comply with the following macronutrient ratio:</p>
  <p class="ratio">65% healthy fats, 25% lean protein, 10% good carbs</p>
</div>

<h2 class="abs section-title" style="top:677px">MEAL PLANNERS</h2>

<article class="abs card" style="left:165px;top:752px">
  <div class="photo" role="img" aria-label="Photo of grilled chicken and peppers in a skillet" style="background:linear-gradient(135deg,#3a2a20,#9a5a2a 50%,#5a7a2a)"></div>
  <h3>Meal Planner Receipe 1</h3>
  <p>Lorem Ipsum is simply dummy text of the print-ing and typesetting industry. Lorem Ipsum has been the industry's standard dummy text ever since the 1500s, when an unknown printer</p>
  <div class="actions"><span class="btn btn-details">View Details</span><span class="btn btn-buy">Buy Now</span></div>
</article>
<article class="abs card" style="left:460px;top:752px">
  <div class="photo" role="img" aria-label="Photo of roast chicken with green beans" style="background:linear-gradient(135deg,#c9a77a,#a35a28 45%,#4f6a2a 80%,#eee)"></div>
  <h3>Meal Planner Receipe 2</h3>
  <p>Lorem Ipsum is simply dummy text of the print-ing and typesetting industry. Lorem Ipsum has been the industry's standard dummy text ever since the 1500s, when an unknown printer</p>
  <div class="actions"><span class="btn btn-details">View Details</span><span class="btn btn-buy">Buy Now</span></div>
</article>
<article class="abs card" style="left:756px;top:752px">
  <div class="photo" role="img" aria-label="Photo of tomato and avocado open sandwich" style="background:linear-gradient(135deg,#f2efe8,#d94a2e 50%,#b9c27a 75%,#f3ece0)"></div>
  <h3>Meal Planner Receipe 3</h3>
  <p>Lorem Ipsum is simply dummy text of the print-ing and typesetting industry. Lorem Ipsum has been the industry's standard dummy text ever since the 1500s, when an unknown printer</p>
  <div class="actions"><span class="btn btn-details">View Details</span><span class="btn btn-buy">Buy Now</span></div>
</article>

<article class="abs card" style="left:165px;top:1153px">
  <div class="photo" role="img" aria-label="Photo of glazed steak with carrots" style="background:linear-gradient(135deg,#fff,#6a3520 45%,#e2782a 75%,#fff)"></div>
  <h3>Meal Planner Receipe 4</h3>
  <p>Lorem Ipsum is simply dummy text of the print-ing and typesetting industry. Lorem Ipsum has been the industry's standard dummy text ever since the 1500s, when an unknown printer</p>
  <div class="actions"><span class="btn btn-details">View Details</span><span class="btn btn-buy">Buy Now</span></div>
</article>
<article class="abs card" style="left:460px;top:1153px">
  <div class="photo" role="img" aria-label="Photo of grilled chicken breast with broccoli and rice" style="background:linear-gradient(135deg,#d9c9a0,#4f7a2a 40%,#c4894a 65%,#f1efe9)"></div>
  <h3>Meal Planner Receipe 5</h3>
  <p>Lorem Ipsum is simply dummy text of the print-ing and typesetting industry. Lorem Ipsum has been the industry's standard dummy text ever since the 1500s, when an unknown printer</p>
  <div class="actions"><span class="btn btn-details">View Details</span><span class="btn btn-buy">Buy Now</span></div>
</article>
<article class="abs card" style="left:756px;top:1153px">
  <div class="photo" role="img" aria-label="Photo of green salad with a wrap" style="background:linear-gradient(135deg,#6aa03a,#3f7a25 45%,#c43a2a 65%,#e9dcc0)"></div>
  <h3>Meal Planner Receipe 6</h3>
  <p>Lorem Ipsum is simply dummy text of the print-ing and typesetting industry. Lorem Ipsum has been the industry's standard dummy text ever since the 1500s, when an unknown printer</p>
  <div class="actions"><span class="btn btn-details">View Details</span><span class="btn btn-buy">Buy Now</span></div>
</article>

<section class="abs testimonials"></section>
<h2 class="abs section-title" style="top:1617px">TESTIMONIALS</h2>
<div class="abs avatar" role="img" aria-label="Portrait photo of the customer"></div>
<p class="abs quote-name">Daniel Rowe</p>
<p class="abs quote-company">Company Name</p>
<p class="abs quote-text">Lorem Ipsum is simply dummy text of the printing and typesetting industry. Lorem Ipsum has been the industry's standard dummy text ever since the 1500s, when an unknown printer took a galley of type and scrambled it to make a type specimen book. It has survived not only five centuries</p>

<section class="abs newsletter">
  <label>Sign up For Newsletter</label>
  <div class="field">Enter Your E-mail</div>
  <div class="submit">SIGN UP</div>
</section>

<ul class="abs footer-col" style="left:165px;top:2403px">
  <li>Home</li><li>About Us</li><li>Meal Plans</li><li>Recipes</li><li>FAQ's</li><li>Contact Us</li>
</ul>
<ul class="abs footer-col" style="left:459px;top:2403px">
  <li>Terms &amp; Conditions</li><li>Legal Notice</li><li>Disclaimer</li><li>Privacy Policy</li>
</ul>
<ul class="abs footer-col social" style="left:876px;top:2388px">
  <li>Chatterly<span class="dot"></span></li>
  <li>Friendwall<span class="dot"></span></li>
  <li>Worknet<span class="dot"></span></li>
</ul>

<p class="abs copyright">© 2014 &nbsp;Company Name ,All Rights reserved</p>

</body>
</html>
```